My project benefits Military, First Responders, Police, Fire, and Educators.

Contact Information for Business Card

2 Sided appointment card. Visual side will have my head shot with "Brisk Lantern" in a bold graffic/text. I am picturing maybe the headshot applied to a filter that has a matrix effect where the picture is made up of data/numbers flowing vertically through the photo. I am of course open to other concepts as well. Side two will have contact info presented in an attractive visual complimenting the front.

```html
<!DOCTYPE html>
<html lang="en">
<head>
<meta charset="utf-8">
<title>Brisk Lantern – Appointment Card</title>
<link rel="stylesheet" href="https://fonts.googleapis.com/css2?family=Source+Sans+3:wght@400;600&display=swap">
<style>
  :root {
    --backdrop: #161616;
    --card-white: #ffffff;
    --brand-green: #14ad72;
    --line-mint: #8fe0c4;
    --logo-grey: #5f5f5f;
    --ink-navy: #1e2a3c;
    --photo-light: #f3f3f3;
    --photo-suit: #1d2438;
  }
  * { margin: 0; padding: 0; box-sizing: border-box; }
  html, body {
    width: 1200px; height: 900px; overflow: hidden;
    background: var(--backdrop);
    font-family: "Source Sans 3", "Myriad Pro", sans-serif;
  }
  .canvas { position: relative; width: 1200px; height: 900px; }
  .card {
    position: absolute; top: 184px; height: 490px;
    border-radius: 12px; overflow: hidden; background: var(--card-white);
  }
  .card--front { left: 299px; width: 301px; }
  .card--back { left: 645px; width: 305px; }

  .headshot {
    height: 309px;
    background: linear-gradient(180deg, var(--photo-light) 0%, var(--photo-light) 55%, #c9c4c0 72%, var(--photo-suit) 86%, var(--photo-suit) 100%);
  }
  .contact-band {
    height: 181px; background: var(--brand-green); color: var(--card-white);
    text-align: center; padding-top: 27px;
  }
  .contact-band__name { font-size: 18px; font-weight: 600; line-height: 22px; }
  .contact-band__title { font-size: 14px; line-height: 16px; }
  .contact-band__details { margin-top: 27px; font-size: 14px; line-height: 18px; }

  .brand {
    margin-top: 55px; text-align: center;
  }
  .brand__mark { display: block; margin: 0 auto; }
  .brand__name {
    margin-top: 10px; font-size: 33px; font-weight: 400; letter-spacing: 0.5px;
    color: var(--logo-grey); line-height: 36px; text-transform: uppercase;
  }
  .appointment__label {
    margin-top: 37px; text-align: center; font-size: 18px; font-weight: 600;
    color: var(--brand-green);
  }
  .appointment__lines { margin: 22px 26px 0; }
  .appointment__line { height: 45px; border-bottom: 1px solid var(--line-mint); }
  .appointment__note {
    margin-top: 26px; text-align: center; font-size: 14.5px; line-height: 18px;
    color: var(--ink-navy);
  }
</style>
</head>
<body>
<main class="canvas">
  <section class="card card--front">
    <div class="headshot" role="img" aria-label="Headshot portrait of the managing director in a dark suit and striped tie"></div>
    <div class="contact-band">
      <p class="contact-band__name">Marcus Delane</p>
      <p class="contact-band__title">Managing Director</p>
      <div class="contact-band__details">
        <p>055-987 321 640</p>
        <p>hello@brisklantern.com</p>
        <p>www.brisklantern.com</p>
      </div>
    </div>
  </section>

  <section class="card card--back">
    <div class="brand">
      <svg class="brand__mark" width="92" height="92" viewBox="0 0 92 92" aria-hidden="true">
        <circle cx="46" cy="46" r="42" fill="none" stroke="var(--logo-grey)" stroke-width="6"/>
      </svg>
      <p class="brand__name">Brisk Lantern</p>
    </div>
    <p class="appointment__label">Appointment</p>
    <div class="appointment__lines">
      <div class="appointment__line"></div>
      <div class="appointment__line"></div>
      <div class="appointment__line"></div>
    </div>
    <p class="appointment__note">If unable to keep appointment,<br>kindly give 24hrs notice.</p>
  </section>
</main>
</body>
</html>
```